Business Card (double-sided) and Stationary Design for dental office

1) Business Card Design: We need a business card design for a dental specialty office.
Texts should contain:
The name of our office "Brindle Oaks Orthodontics"
Tagline: "Specialist in Orthodontic and Maxillofacial Orthopedics"
Tag line: "Creating "Tolvering" smiles for Children and Adults"
Doctor name: "Doctor Name"
Office Address:
"123 Street Name
City, State Zip code"
Office email address: office@brindleoaksortho.com
Website: www.brindleoaksortho.com

We will provide the full office address once the design is selected
Theme: beach, paradise, coastal, wave
We would like to have some creativity in design. Some acceptable ideas: front page: logo and office name. Back page: more detail information, and map to office in form of an island. Please see sample from our other location, but you DON'T HAVE TO USE OR COPY THE SAME CONCEPT.

IF POSSIBLE, PLEASE SUBMIT AT LEAST TWO CONCEPTS: ONE WITH THE BACK LOOKING SIMILAR TO WHAT IS IN THE SAMPLE, AND ONE DIFFERENT.

Color: designer to choose. We have different shade of blues and sand color in our office. Please see logo.

2) Please also design a matching set of stationary that compliment the business card and our logo.

Target Market(s)

Dental

Contact Information for Business Card

See descriptions

Font styles to use
Other font styles liked:
• Matching texts in logo

Colors
0054AA
0677BA
7BADD7
CADEEF
E8F1F8
0094D4
00A9DD
6FCCEA
C7EBF8
E9F6FB
00AB8E
00BBA5
67D7C9
C6EFE9
E9F9F6

Requirements
Must have
• Double-sided
Nice to have
• Beach coastal theme
Should not have
• Any shape or drawing of of tooth or teeth. We don’t need these. You don't necessarily have to just cut and paste the logo art and text as a whole, you have the liberty to rearrange the text.

```html
<!DOCTYPE html>
<html lang="en">
<head>
<meta charset="utf-8">
<title>Brindle Oaks Orthodontics – Envelope</title>
<link href="https://fonts.googleapis.com/css2?family=Montserrat:wght@700;800&family=Roboto+Slab:wght@400;700&display=swap" rel="stylesheet">
<style>
  :root {
    --brand-blue: #2757a3;
    --flap-mark: #3a63ab;
    --paper: #ffffff;
    --scene-tint: #e6e8f3;
    --mark-teal: #3f7b8b;
    --ink: #111111;
  }
  * { margin: 0; padding: 0; box-sizing: border-box; }
  html, body {
    width: 1200px; height: 825px; overflow: hidden;
    background: var(--brand-blue);
  }
  .envelope {
    position: relative;
    width: 1200px; height: 825px;
    background: var(--brand-blue);
  }
  .envelope__body {
    position: absolute;
    left: 12px; top: 10px; right: 12px; bottom: 10px;
    background: var(--paper);
    overflow: hidden;
  }
  .coastal-scene {
    position: absolute;
    left: 0; right: 0; top: 320px; bottom: 0;
    background:
      radial-gradient(ellipse 420px 330px at 980px 300px, var(--scene-tint) 0%, rgba(230,232,243,0.6) 60%, rgba(230,232,243,0) 100%),
      linear-gradient(to bottom, rgba(230,232,243,0) 0%, rgba(230,232,243,0.5) 55%, var(--scene-tint) 85%);
  }
  .flap {
    position: absolute; left: 0; top: 0;
    width: 1200px; height: 400px;
  }
  .flap-mark {
    position: absolute;
    left: 521px; top: 82px;
    width: 154px; height: 154px;
    border-radius: 50%;
    background: var(--flap-mark);
    display: flex; align-items: center; justify-content: center;
    text-align: center;
    font-family: "Montserrat", sans-serif;
    font-weight: 800;
    font-size: 17px;
    line-height: 1.15;
    color: var(--brand-blue);
  }
  .brand-mark {
    position: absolute;
    left: 55px; top: 606px;
    width: 156px; height: 156px;
    border-radius: 50%;
    background: var(--mark-teal);
    display: flex; align-items: center; justify-content: center;
    text-align: center;
    font-family: "Montserrat", sans-serif;
    font-weight: 800;
    font-size: 19px;
    line-height: 1.15;
    color: var(--paper);
  }
  .return-address {
    position: absolute;
    left: 245px; top: 600px;
    color: var(--ink);
  }
  .return-address__practice {
    font-family: "Montserrat", sans-serif;
    font-weight: 800;
    font-size: 21px;
    letter-spacing: 0.5px;
    text-transform: uppercase;
    line-height: 1;
  }
  .return-address__doctor {
    margin-top: 20px;
    font-family: "Roboto Slab", serif;
    font-weight: 700;
    font-size: 20px;
    letter-spacing: 0.8px;
    text-transform: uppercase;
    line-height: 1;
  }
  .return-address__street,
  .return-address__contact {
    font-family: "Roboto Slab", serif;
    font-weight: 400;
    font-size: 18.5px;
    letter-spacing: 0.8px;
  }
  .return-address__street { margin-top: 18px; line-height: 1; }
  .return-address__contact { margin-top: 14px; line-height: 26px; }
</style>
</head>
<body>
  <div class="envelope">
    <div class="envelope__body">
      <div class="coastal-scene" role="img" aria-label="Faint coastal illustration: waves, whale tail, coconut drink, sailing ship, seaweed, palm trees and seabirds"></div>
    </div>

    <svg class="flap" viewBox="0 0 1200 400" aria-hidden="true">
      <polygon points="0,0 1200,0 1200,10 1188,10 600,388 12,10 0,10" fill="var(--brand-blue)"/>
    </svg>
    <div class="flap-mark">Brindle<br>Oaks</div>

    <div class="brand-mark">Brindle<br>Oaks</div>

    <address class="return-address" style="font-style: normal;">
      <p class="return-address__practice">Brindle Oaks Orthodontics</p>
      <p class="return-address__doctor">Doctor Name</p>
      <p class="return-address__street">123 Street Name City, State Zip code</p>
      <p class="return-address__contact">office@brindleoaksortho.com<br>www.brindleoaksortho.com</p>
    </address>
  </div>
</body>
</html>
```